MRT Property - Business Cards

Looking for a business card & general letterhead, signage etc design for our new logo.

Colours:
000a20
0056a2
00b5ef
0088ce
68cef2

Fonts:
Poppins
Karla

Please keep look and feel of new brand - example in the zip package I sent.

```html
<!DOCTYPE html>
<html lang="en">
<head>
<meta charset="utf-8">
<title>MRT Property – Business Cards</title>
<link href="https://fonts.googleapis.com/css2?family=Montserrat:wght@400;600;700&display=swap" rel="stylesheet">
<style>
  :root {
    --stage: #6f5a45;
    --card-front: #ffffff;
    --card-back: #0f1426;
    --brand-deep: #0056a2;
    --brand-mid: #0088ce;
    --brand-sky: #29abe2;
    --brand-light: #68cef2;
    --ink: #2d2d2d;
    --muted: #6a6a6a;
  }
  html, body {
    margin: 0;
    padding: 0;
    width: 900px;
    height: 1200px;
    overflow: hidden;
    background: var(--stage);
    font-family: "Montserrat", sans-serif;
  }
  .canvas {
    position: relative;
    width: 900px;
    height: 1200px;
  }
  .card {
    position: absolute;
    left: 80px;
    width: 742px;
    height: 440px;
    border-radius: 40px;
    box-shadow: 0 6px 14px rgba(0,0,0,0.45);
  }
  .card--front { top: 132px; background: var(--card-front); }
  .card--back  { top: 638px; background: var(--card-back); }

  .brand {
    position: absolute;
    display: flex;
    align-items: center;
    gap: 14px;
  }
  .brand__dot {
    border-radius: 50%;
    background: var(--brand-sky);
    flex: none;
  }
  .brand__name {
    font-weight: 700;
    color: var(--brand-deep);
    white-space: nowrap;
    letter-spacing: 0.5px;
  }
  .card--front .brand { left: 32px; top: 205px; }
  .card--front .brand__dot { width: 34px; height: 34px; }
  .card--front .brand__name { font-size: 38px; }

  .card--back .brand { left: 50%; top: 200px; transform: translateX(-50%); gap: 20px; }
  .card--back .brand__dot { width: 52px; height: 52px; }
  .card--back .brand__name { font-size: 60px; }

  .divider {
    position: absolute;
    left: 409px;
    top: 138px;
    width: 2px;
    height: 182px;
    background: var(--brand-sky);
  }
  .contact {
    position: absolute;
    left: 456px;
    top: 132px;
    color: var(--ink);
  }
  .contact__name {
    margin: 0;
    font-size: 27px;
    font-weight: 600;
    color: var(--brand-sky);
    line-height: 1.1;
  }
  .contact__role {
    margin: 0 0 18px;
    font-size: 16px;
    color: var(--muted);
  }
  .contact__list {
    list-style: none;
    margin: 0 0 12px;
    padding: 0;
  }
  .contact__item {
    display: flex;
    align-items: center;
    gap: 12px;
    font-size: 16px;
    line-height: 22.5px;
  }
  .contact__icon { width: 14px; height: 14px; flex: none; }
  .contact__address {
    margin: 0;
    font-style: normal;
    font-size: 16px;
    line-height: 20px;
    padding-left: 2px;
  }
</style>
</head>
<body>
<main class="canvas">
  <section class="card card--front" aria-label="Business card front">
    <div class="brand">
      <span class="brand__dot"></span>
      <span class="brand__name">MRT Property</span>
    </div>
    <div class="divider"></div>
    <div class="contact">
      <h1 class="contact__name">Corin Halvorsen</h1>
      <p class="contact__role">Owner</p>
      <ul class="contact__list">
        <li class="contact__item">
          <svg class="contact__icon" viewBox="0 0 14 14"><path fill="#29abe2" d="M1 5c0-2 2-3 6-3s6 1 6 3v1h-3V4.5H4V6H1zM3 7h8l1.5 5h-11z"/><circle cx="7" cy="9.3" r="1.4" fill="#fff"/></svg>
          <span>215-555-0142</span>
        </li>
        <li class="contact__item">
          <svg class="contact__icon" viewBox="0 0 14 14"><rect x="1" y="3" width="12" height="8" fill="#29abe2"/><path d="M1 3l6 4.5L13 3" fill="none" stroke="#fff" stroke-width="1.2"/></svg>
          <span>info@mrtproperty.com.au</span>
        </li>
        <li class="contact__item">
          <svg class="contact__icon" viewBox="0 0 14 14"><circle cx="7" cy="7" r="6" fill="#29abe2"/><path d="M1 7h12M7 1c-2.5 3-2.5 9 0 12M7 1c2.5 3 2.5 9 0 12" fill="none" stroke="#fff" stroke-width="0.9"/></svg>
          <span>www.mrtproperty.com.au</span>
        </li>
      </ul>
      <address class="contact__address">48 Harbor Lane, Suite 210<br>Marlow, PA 18920</address>
    </div>
  </section>

  <section class="card card--back" aria-label="Business card back">
    <div class="brand">
      <span class="brand__dot"></span>
      <span class="brand__name">MRT Property</span>
    </div>
  </section>
</main>
</body>
</html>
```